Harborview Estates Business Card for Apartment Buildings

Create business cards for resident managers who run apartment buildings. The audience is the public who are searching for apartment rentals, and current residents who live at the apartment building. Key design element will be incorporating the company logo, however, the logo cannot dominate. The building name and manager name are more important than the logo. Current business card design leaves little room for copy, so we may need to reduce the size on the current card to allow for more space for copy.

Target Market(s)

Adults 18-65 years of age, who are looking for an apartment rental, plus current residents who live at our apartment buildings.

Industry/Entity Type

Property Management

Contact Information for Business Card

A major design element will be use of the company logo. Important property and manager contact information must be part of the design. The size of the logo will need to be reduced to make room for building and manager contact copy.

Font styles to use
Sans Serif

Colors
3176b5
000000
959595
ffffff

Requirements
Must have
• 1) Incorporate the company logo.
• 2) Use the company colors (dark blue, black/grey, over white).
• 3) FEATURE THE BUILDING NAME
• 4) FEATURE THE MANAGER NAME
• 5) The company name is less important than BUILDING and MANAGER
• 6) Manager contact information
• **SEE ATTACHED CREATIVE BRIEF**
Nice to have
• 1) Back of card logo watermark
• 2) Ability to write notes on back of carfd
Should not have
• Avoid letting the company logo dominate the card, the building name and manager are more important than the company logo.

```html
<!DOCTYPE html>
<html lang="en">
<head>
<meta charset="utf-8">
<title>Harborview Estates – Business Card</title>
<link href="https://fonts.googleapis.com/css2?family=Mulish:wght@400;600;800&display=swap" rel="stylesheet">
<style>
  :root{
    --brand-blue:#3176b5;
    --deep-blue:#1f62a3;
    --back-blue:#2a7ab8;
    --ink:#000000;
    --grey:#5f5f5f;
    --light-grey:#959595;
    --paper:#ffffff;
    --stage:#e9ecef;
    --watermark:#dbe8f2;
  }
  *{margin:0;padding:0;box-sizing:border-box}
  html,body{width:1200px;height:862px;overflow:hidden}
  body{background:var(--stage);font-family:"Mulish",Arial,sans-serif;position:relative}
  .card{position:absolute;left:260px;width:680px;height:389px;border-radius:4px;overflow:hidden;box-shadow:0 6px 18px rgba(0,0,0,.15)}
  .card--back{top:30px;background:linear-gradient(135deg,#2470ae 0%,var(--back-blue) 60%,#3386c2 100%);display:flex;align-items:center;justify-content:center}
  .card--front{top:443px;background:var(--paper)}
  .back-mark{display:flex;align-items:center;gap:16px}
  .back-mark__dot{width:58px;height:58px;border-radius:50%;background:#226aa5}
  .back-mark__name{font-weight:800;font-size:40px;letter-spacing:1px;color:#1c5f9b;text-transform:uppercase}
  .watermark{position:absolute;right:-90px;top:60px;width:380px;height:380px;border-radius:50%;background:var(--watermark)}
  .brand{position:absolute;right:40px;top:34px;display:flex;align-items:center;gap:10px}
  .brand__dot{width:34px;height:34px;border-radius:50%;background:var(--brand-blue)}
  .brand__name{font-weight:800;font-size:24px;line-height:1.2;color:var(--brand-blue);text-transform:uppercase;letter-spacing:.5px}
  .accent-bar{position:absolute;left:0;top:162px;width:6px;height:34px;background:var(--brand-blue)}
  .details{position:absolute;left:46px;top:96px}
  .manager-name{font-weight:800;font-size:22px;line-height:1.25;color:var(--brand-blue);text-transform:uppercase;letter-spacing:.5px}
  .manager-title{font-size:13px;line-height:1.3;color:var(--grey);margin-top:3px}
  .building-name{font-weight:600;font-size:16px;line-height:1.25;color:var(--brand-blue);margin-top:20px}
  .address{font-size:15px;color:var(--grey);line-height:1.4;margin-top:4px}
  .contacts{list-style:none;margin-top:12px}
  .contacts li{display:flex;align-items:center;gap:10px;font-size:14px;color:var(--grey);line-height:1.5}
  .contacts svg{width:14px;height:14px;fill:var(--deep-blue);flex:none}
</style>
</head>
<body>
  <section class="card card--back" aria-label="Card back">
    <div class="back-mark">
      <span class="back-mark__dot"></span>
      <span class="back-mark__name">Harborview Estates</span>
    </div>
  </section>

  <section class="card card--front" aria-label="Card front">
    <div class="watermark" aria-hidden="true"></div>
    <div class="brand">
      <span class="brand__dot"></span>
      <span class="brand__name">Harborview Estates</span>
    </div>
    <div class="accent-bar"></div>
    <div class="details">
      <h1 class="manager-name">Marisol Delgado</h1>
      <p class="manager-title">Resident Manager</p>
      <h2 class="building-name">Bayside Court Apartments</h2>
      <p class="address">1482 Linden Avenue San<br>Diego, CA 92104</p>
      <ul class="contacts">
        <li><svg viewBox="0 0 16 16"><path d="M3.5 1l2.5 3-1.5 2c1 2 3 4 5 5l2-1.5 3 2.5-1.5 2.5C8 15 1 8 1 2.5z"/></svg>619-555-0142</li>
        <li><svg viewBox="0 0 16 16"><path d="M4 1h8v4H4zM1 6h14v6h-3v3H4v-3H1zM5 10v3h6v-3z"/></svg>619-555-0187</li>
        <li><svg viewBox="0 0 16 16"><path d="M4 0h8a1 1 0 0 1 1 1v14a1 1 0 0 1-1 1H4a1 1 0 0 1-1-1V1a1 1 0 0 1 1-1zm1 2v10h6V2zm3 11a1 1 0 1 0 0 2 1 1 0 0 0 0-2z"/></svg>619-555-0123</li>
        <li><svg viewBox="0 0 16 16"><path d="M1 3h14v10H1zm1.5 1.5v.3L8 9l5.5-4.2v-.3zm0 2.2v4.8h11V6.7L8 11z"/></svg>marisol@harborviewest.com</li>
      </ul>
    </div>
  </section>
</body>
</html>
```